I need an Office Furniture selling website

My office furniture store is driven by creativity and innovation. With this i am searching for an industry standard website for my office furniture and items selling website. I sell a wide range of office furniture items such as chairs, tables, burglary, cotton, wardrobe, etc. There will be a category for each of the items i sell. My business is based in the United States and services only US based residents. I don't accept online payments and customers are to pay on delivery of items. The website is to have images of the items i sell. I would like brown, black and golden colors because those are the colors furniture mostly make use of. Designs submitted should be unique.

Industry/Entity Type

Furniture Store

Coding

Coded - Design and coding required

```html
<!DOCTYPE html>
<html lang="en">
<head>
<meta charset="utf-8">
<title>Harwell Office Furniture</title>
<link href="https://fonts.googleapis.com/css2?family=Open+Sans:wght@400;600;700;800&display=swap" rel="stylesheet">
<style>
:root{
  --gold:#b8955a;
  --brown:#6b3d14;
  --dark:#161616;
  --darker:#0f0f0f;
  --ink:#333333;
  --muted:#666666;
  --light:#f1f1f1;
  --white:#ffffff;
}
*{box-sizing:border-box;margin:0;padding:0}
html,body{width:1200px;height:2586px;overflow:hidden}
body{font-family:"Open Sans",Arial,sans-serif;color:var(--ink);background:var(--white);position:relative}
.abs{position:absolute}

/* top bar */
.topbar{left:0;top:0;width:1200px;height:62px;background:var(--light)}
.brand-block{left:0;top:0;width:405px;height:62px;background:var(--dark)}
.brand{font-weight:800;font-size:34px;letter-spacing:1px;color:var(--gold);line-height:62px;padding-left:74px}
.top-contact{right:74px;top:0;height:62px;display:flex;align-items:center;gap:26px;font-size:11px;font-weight:600;color:var(--brown)}
.top-contact span{display:flex;align-items:center;gap:8px}

/* nav */
.nav{left:0;top:62px;width:1200px;height:72px;border-bottom:1px solid #e3e3e3;display:flex;align-items:center;padding-left:74px;gap:0}
.nav a{font-size:12px;font-weight:600;color:var(--ink);text-decoration:none;text-transform:uppercase;margin-right:44px}

/* hero */
.hero{left:0;top:134px;width:1200px;height:525px;background:linear-gradient(100deg,#6b4a35 0%,#c9c4bd 35%,#e8e6e2 50%,#8c2a1a 75%,#5a2a1a 100%)}
.hero-panel{left:0;top:207px;width:420px;height:379px;background:rgba(10,10,10,.9);padding:88px 0 0 74px}
.hero-panel h1{font-size:37px;font-weight:800;line-height:40px;color:var(--gold);text-transform:uppercase}
.hero-panel h1 b{display:block;color:var(--white)}
.hero-panel p{font-size:23px;color:var(--white);line-height:31px;margin-top:10px;width:300px}
.btn{display:inline-block;background:var(--gold);color:var(--white);font-size:11px;font-weight:600;text-transform:uppercase;text-align:center}
.hero-panel .btn{margin-top:22px;width:127px;height:35px;line-height:35px}
.arrow{width:34px;height:34px;background:#7a5428;display:flex;align-items:center;justify-content:center;left:400px}

/* headings */
.section-title{font-size:19px;font-weight:700;text-transform:uppercase;letter-spacing:.5px}

/* categories */
.cat{overflow:hidden}
.cat-label{position:absolute;background:rgba(20,20,20,.85);text-align:center;color:var(--white)}
.cat-label h3{font-size:34px;font-weight:700;line-height:40px}
.cat-label .btn{width:127px;height:32px;line-height:32px;font-size:11px;margin-top:8px}

/* products */
.products{left:0;top:1350px;width:1200px;height:474px;background:linear-gradient(90deg,#1d1d1d,#111 20%,#1e1e1e 40%,#121212 60%,#1c1c1c 80%,#101010)}
.card{top:1453px;width:243px;height:319px;background:var(--white);text-align:center}
.card .pic{margin:20px auto 0;width:190px;height:200px;border-radius:4px}
.card h4{font-size:16px;font-weight:700;color:var(--brown);margin-top:15px}
.card .price{font-size:17px;font-weight:600;color:var(--ink);margin-top:2px}

/* welcome */
.welcome{left:74px;top:1862px;width:490px}
.welcome h2{font-size:20px;color:var(--brown)}
.welcome p{font-size:14px;line-height:24px;color:var(--muted);margin-top:14px}
.btn-dark{display:inline-block;background:#3a3a3a;color:var(--white);font-size:12px;font-weight:600;text-transform:uppercase;width:127px;height:35px;line-height:35px;text-align:center;margin-top:40px}
.promo{top:1870px;width:255px;height:223px;background:var(--gold);text-align:center}
.promo .kicker{font-size:25px;font-weight:700;color:var(--white);margin-top:18px}
.promo .big{font-size:62px;font-weight:800;color:var(--brown);line-height:66px}
.promo .big small{font-size:24px;color:var(--white);font-style:normal}
.promo .note{font-size:15px;font-weight:700;color:var(--white)}
.promo .btn-dark{margin-top:14px;background:#2a2a2a;width:138px;height:44px;line-height:44px}

/* newsletter */
.newsletter{left:0;top:2141px;width:1200px;height:186px;background:#ececec;text-align:center}
.newsletter h2{font-size:20px;font-weight:700;color:var(--brown);text-transform:uppercase;margin-top:40px}
.field{left:343px;top:93px;width:362px;height:45px;background:var(--white);font-size:10px;color:#888;text-align:left;padding-left:22px;line-height:45px;text-transform:uppercase}
.subscribe{left:717px;top:93px;width:140px;height:45px;line-height:45px}

/* footer */
.footer{left:0;top:2327px;width:1200px;height:259px;background:linear-gradient(90deg,#161616,#0e0e0e 30%,#1a1a1a 55%,#101010 80%,#171717)}
.footer .brand{font-size:29px;line-height:30px;padding:0}
.footer p{font-size:11px;color:#bdbdbd;line-height:21px}
.footer h5{font-size:14px;font-weight:700;color:var(--gold);text-transform:uppercase;margin-bottom:14px}
.footer ul{list-style:none}
.footer li{font-size:13px;color:#d8d8d8;line-height:26px}
.social{display:flex;gap:14px}
.social span{width:12px;height:12px;border-radius:50%;background:var(--gold)}
</style>
</head>
<body>

<header>
  <div class="abs topbar"></div>
  <div class="abs brand-block"><div class="brand">HARWELL</div></div>
  <div class="abs top-contact">
    <span><svg width="11" height="11" viewBox="0 0 24 24"><path fill="#6b3d14" d="M6.6 10.8a15 15 0 006.6 6.6l2.2-2.2c.3-.3.7-.4 1-.2 1.1.4 2.3.6 3.6.6.6 0 1 .4 1 1V20c0 .6-.4 1-1 1A17 17 0 013 4c0-.6.4-1 1-1h3.5c.6 0 1 .4 1 1 0 1.3.2 2.5.6 3.6.1.3 0 .7-.2 1z"/></svg>1-800-555-0142</span>
    <span><svg width="14" height="11" viewBox="0 0 28 20"><path fill="#6b3d14" d="M0 2h17v13H0zM18 6h6l4 5v4h-10z"/><circle cx="6" cy="17" r="3" fill="#6b3d14"/><circle cx="22" cy="17" r="3" fill="#6b3d14"/></svg>FREE SHIPPING</span>
  </div>
  <nav class="abs nav">
    <a>Home</a><a>Chairs</a><a>Tables</a><a>Burglary</a><a>Cotton</a><a>Wardrobe</a><a>Specials</a><a>Store Location</a><a>Blog</a><a>Contact Us</a>
  </nav>
</header>

<section>
  <div class="abs hero" role="img" aria-label="Executive office with red wooden desk, black leather chairs and cabinets"></div>
  <div class="abs hero-panel">
    <h1>Welcome to <b>Harwell</b></h1>
    <p>We are an office furniture selling company..</p>
    <span class="btn">Shop Now</span>
  </div>
  <div class="abs arrow" style="top:354px"><svg width="12" height="14" viewBox="0 0 12 14"><path d="M9 1L3 7l6 6" stroke="#fff" stroke-width="2.5" fill="none"/></svg></div>
  <div class="abs arrow" style="top:401px"><svg width="12" height="14" viewBox="0 0 12 14"><path d="M3 1l6 6-6 6" stroke="#fff" stroke-width="2.5" fill="none"/></svg></div>
</section>

<section>
  <h2 class="abs section-title" style="left:74px;top:732px;color:var(--brown)">Featured Categories</h2>

  <div class="abs cat" style="left:74px;top:786px;width:514px;height:521px;background:linear-gradient(160deg,#e9e9e9,#8a7566 55%,#4e3b30)" role="img" aria-label="Office desk with drawer unit">
    <div class="cat-label" style="left:128px;top:400px;width:258px;height:121px;padding-top:12px"><h3>Tables</h3><span class="btn">Shop Now</span></div>
  </div>
  <div class="abs cat" style="left:600px;top:786px;width:255px;height:252px;background:linear-gradient(150deg,#8a8580,#3a3532)" role="img" aria-label="Close-up of security lock">
    <div class="cat-label" style="left:64px;top:130px;width:191px;height:107px;padding-top:12px"><h3>Burglary</h3><span class="btn">Shop Now</span></div>
  </div>
  <div class="abs cat" style="left:871px;top:786px;width:255px;height:252px;background:linear-gradient(150deg,#dfe6cf,#7aa23a 50%,#4b5a34)" role="img" aria-label="Green lounge chairs">
    <div class="cat-label" style="left:32px;top:130px;width:191px;height:107px;padding-top:12px"><h3>Chairs</h3><span class="btn">Shop Now</span></div>
  </div>
  <div class="abs cat" style="left:600px;top:1055px;width:255px;height:252px;background:linear-gradient(120deg,#4a4846,#c6c0b8 60%,#a38563)" role="img" aria-label="Cotton jar on desk">
    <div class="cat-label" style="left:64px;top:130px;width:191px;height:107px;padding-top:12px"><h3>Cotton</h3><span class="btn">Shop Now</span></div>
  </div>
  <div class="abs cat" style="left:871px;top:1055px;width:255px;height:252px;background:linear-gradient(120deg,#8b5a2b,#4d5563 45%,#a06a35)" role="img" aria-label="Wooden wardrobe with glass doors">
    <div class="cat-label" style="left:0;top:130px;width:255px;height:107px;padding-top:12px"><h3>Wardrobe</h3><span class="btn">Shop Now</span></div>
  </div>
</section>

<section>
  <div class="abs products"></div>
  <h2 class="abs section-title" style="left:74px;top:1393px;color:var(--white)">Featured Products</h2>
  <svg class="abs" style="left:1092px;top:1399px" width="34" height="14" viewBox="0 0 34 14"><path d="M7 1L2 7l5 6" stroke="#fff" stroke-width="2" fill="none"/><path d="M27 1l5 6-5 6" stroke="#b8955a" stroke-width="2" fill="none"/></svg>

  <div class="abs card" style="left:74px"><div class="pic" role="img" aria-label="Black office chair" style="background:radial-gradient(circle,#3a3a3a 30%,#fff 72%)"></div><h4>Product Name Here</h4><div class="price">$00.00</div></div>
  <div class="abs card" style="left:343px"><div class="pic" role="img" aria-label="Wooden bookshelf" style="background:radial-gradient(circle,#c8955a 30%,#fff 72%)"></div><h4>Product Name Here</h4><div class="price">$00.00</div></div>
  <div class="abs card" style="left:615px"><div class="pic" role="img" aria-label="Executive desk with chair" style="background:radial-gradient(circle,#6a3a22 30%,#fff 72%)"></div><h4>Product Name Here</h4><div class="price">$00.00</div></div>
  <div class="abs card" style="left:884px"><div class="pic" role="img" aria-label="Wooden writing desk with drawers" style="background:radial-gradient(circle,#b06a3a 30%,#fff 72%)"></div><h4>Product Name Here</h4><div class="price">$00.00</div></div>
</section>

<section>
  <div class="abs welcome">
    <h2 class="section-title" style="color:var(--brown)">Welcome Harwell</h2>
    <p>Vestibulum vel metus sit amet turpis bibendum tincidunt vel sit amet quam. Pellentesque habitant morbi tristique senectus et netus et malesuada fames ac turpis egestas. Nunc consequat congue nulla eu imperdiet. Donec in est erat, id malesuada turpis. Nunc a dui id turpis convallis semper. Nunc dignissim lectus vitae eros placerat euismod.</p>
    <span class="btn-dark">Read More</span>
  </div>
  <div class="abs promo" style="left:600px">
    <div class="kicker">WARDROBE</div>
    <div class="big">20%<small>OFF</small></div>
    <div class="note">Shopping Above $1000</div>
    <span class="btn-dark">Shop Now</span>
  </div>
  <div class="abs promo" style="left:871px">
    <div class="kicker" style="line-height:30px">FREE</div>
    <div class="big" style="font-size:44px;line-height:46px">SHIPPING</div>
    <svg width="90" height="68" viewBox="0 0 28 20" style="margin-top:8px"><path fill="#fff" d="M0 2h17v13H0zM18 6h6l4 5v4h-10z"/><circle cx="6" cy="17" r="3" fill="#fff"/><circle cx="22" cy="17" r="3" fill="#fff"/></svg>
    <div class="note" style="margin-top:6px">Shipping Over $560</div>
  </div>
</section>

<section class="abs newsletter">
  <h2>Join Our Newsletter</h2>
  <div class="abs field">Enter Email Address</div>
  <span class="abs btn subscribe">Subscribe</span>
</section>

<footer class="abs footer">
  <div class="abs" style="left:74px;top:46px">
    <div class="brand">HARWELL</div>
    <p style="margin-top:12px">Copyright © 2016. Company Name<br>All Right Reserved</p>
    <div class="social" style="margin-top:18px"><span></span><span></span><span></span><span></span><span></span><span></span></div>
  </div>
  <div class="abs" style="left:359px;top:46px">
    <h5>Navigation</h5>
    <div style="display:flex;gap:70px">
      <ul><li>Home</li><li>Chairs</li><li>Tables</li><li>Burglary</li><li>Cotton</li><li>Wardrobe</li></ul>
      <ul><li>Blog</li><li>Specials</li><li>Store Location</li><li>Contact Us</li></ul>
    </div>
  </div>
  <div class="abs" style="left:679px;top:46px">
    <h5>Account</h5>
    <ul><li>Log In</li><li>Register</li><li>Wishlist</li><li>My Account</li><li>My Cart</li></ul>
  </div>
  <div class="abs" style="left:894px;top:46px">
    <h5>Other Links</h5>
    <ul><li>Return Policy</li><li>Free Shipping</li><li>Gift Certificate</li><li>Testimonials</li></ul>
  </div>
</footer>

</body>
</html>
```